Business Card For Halvenmoor Financial Consulting

Hi, I would like a business card designed. Bold, modern.
Please use the same design as the logo. I have also attached the website design to see the overall theme.
Wordmark Font
Color: Hex: #01AEF7

```html
<!DOCTYPE html>
<html lang="en">
<head>
<meta charset="utf-8">
<title>Halvenmoor Financial Consulting – Business Card</title>
<link href="https://fonts.googleapis.com/css2?family=Montserrat:wght@400;600;700&display=swap" rel="stylesheet">
<style>
  :root {
    --stage: #3b3b3c;
    --card: #16212b;
    --card-deep: #111a22;
    --accent: #01aef7;
    --text: #e9eef2;
    --muted: #b9c4cc;
  }
  * { margin: 0; padding: 0; box-sizing: border-box; }
  html, body { width: 1200px; height: 801px; overflow: hidden; }
  body {
    background: var(--stage);
    font-family: "Montserrat", Arial, sans-serif;
    position: relative;
  }
  .card {
    position: absolute;
    top: 252px;
    width: 520px;
    height: 297px;
    background: var(--card);
    border-bottom: 3px solid var(--accent);
    overflow: hidden;
  }
  .card--front { left: 60px; }
  .card--back { left: 620px; }

  /* Brand lockup */
  .brand {
    display: flex;
    align-items: center;
    gap: 12px;
  }
  .brand__square {
    width: 30px;
    height: 30px;
    border: 3px solid var(--accent);
    flex: none;
  }
  .brand__name {
    font-weight: 700;
    color: var(--text);
    letter-spacing: 0.06em;
    text-transform: uppercase;
    line-height: 1.15;
  }

  /* Front side */
  .card--front .brand {
    position: absolute;
    left: 34px;
    top: 118px;
  }
  .card--front .brand__name { font-size: 17px; }
  .divider {
    position: absolute;
    left: 262px;
    top: 40px;
    width: 1px;
    height: 217px;
    background: var(--accent);
    opacity: 0.7;
  }
  .contact {
    position: absolute;
    left: 284px;
    top: 58px;
    color: var(--text);
    font-size: 12px;
    line-height: 1.45;
  }
  .contact__name {
    font-size: 16px;
    font-weight: 700;
    color: var(--accent);
    text-transform: uppercase;
    letter-spacing: 0.02em;
  }
  .contact__title { color: var(--muted); margin-bottom: 14px; }
  .contact__address { margin-bottom: 14px; }
  .contact__line { display: flex; align-items: center; gap: 7px; }
  .contact__line svg { width: 11px; height: 11px; flex: none; }

  /* Back side */
  .card__texture {
    position: absolute;
    inset: 0;
    background: linear-gradient(120deg, #2b3c4c 0%, #1a2733 40%, var(--card-deep) 100%);
  }
  .card--back .brand {
    position: absolute;
    left: 50%;
    top: 50%;
    transform: translate(-50%, -50%);
  }
  .card--back .brand__square { width: 40px; height: 40px; }
  .card--back .brand__name { font-size: 24px; }
</style>
</head>
<body>

<section class="card card--front" aria-label="Business card front">
  <div class="brand">
    <span class="brand__square"></span>
    <span class="brand__name">Halvenmoor<br>Consulting</span>
  </div>
  <div class="divider"></div>
  <div class="contact">
    <p class="contact__name">Marlo Tenvick</p>
    <p class="contact__title">President</p>
    <p class="contact__address">1180 Seacliff Row<br>Larkspur Bay CA 90412</p>
    <p class="contact__line">
      <svg viewBox="0 0 12 12" aria-hidden="true"><path d="M3 1l2 2.5-1.2 1.2a7 7 0 0 0 3.5 3.5L8.5 7 11 9l-1.5 2C5 11 1 7 1 2.5z" fill="var(--accent)"/></svg>
      555-014-2290
    </p>
    <p class="contact__line">
      <svg viewBox="0 0 12 12" aria-hidden="true"><rect x="1" y="2.5" width="10" height="7" fill="var(--accent)"/><path d="M1 2.5l5 4 5-4" stroke="var(--card)" fill="none"/></svg>
      info@HalvenmoorConsulting.com
    </p>
    <p class="contact__line">
      <svg viewBox="0 0 12 12" aria-hidden="true"><circle cx="6" cy="6" r="5" fill="var(--accent)"/><path d="M1 6h10M6 1c-2.5 3-2.5 7 0 10M6 1c2.5 3 2.5 7 0 10" stroke="var(--card)" stroke-width="0.8" fill="none"/></svg>
      www.HalvenmoorConsulting.com
    </p>
  </div>
</section>

<section class="card card--back" aria-label="Business card back">
  <div class="card__texture" role="img" aria-label="Embossed repeating brand pattern in dark navy tones"></div>
  <div class="brand">
    <span class="brand__square"></span>
    <span class="brand__name">Halvenmoor<br>Consulting</span>
  </div>
</section>

</body>
</html>
```